BrivoTerna. Lantern of the Steady Harvest. Business card

Professional business card for BrivoTerna (Lantern of the Steady Harvest)
My rationale: Strategy-> Execution-> Results-> Value that lead to the BrivoTerna name: We put the Lantern of the Steady Harvest.
We deliver value to our customers helping them at defining a good strategy (cyan arrow). 90% of well formulated strategies fail due to poor execution so we also consider strategical execution very important (green arrow). Due to the execution we obtain the results (blue arrow). Finally, the results provide feedback to redefine strategy, and the new strategy has to be executed and new results obtained providing new feedback and on and on. It's like a wheel that finally, must create corporate value: value for shareholders, staholders, employees, providers...-

Target Market(s)

CEOs and steering comitees , invewrnent funds

Industry/Entity Type

Business Consultant

Contact Information for Business Card

Teodoro Vinsquel
CEO & Founder
teodoro.vinsquel@brivoterna-example.com
Mobile: +34 655.803.912
www.brivoterna-example.com

Colors

Designer to choose colors to be used in the design.

Requirements
Nice to have
• Nice to hace the words: Strategy, execution, results
• Nice to vave the claim: Lantern of the Steady Harvest
• The three colors should be shown:
• cyan for STRATEGY
• green for EXECUTION
• blue for RESULTS
Should not have
• Complete black background

```html
<!DOCTYPE html>
<html lang="en">
<head>
<meta charset="utf-8">
<title>BrivoTerna – Business Card</title>
<link href="https://fonts.googleapis.com/css2?family=Arimo:wght@400;700&display=swap" rel="stylesheet">
<style>
  :root {
    --navy: #223f94;
    --green: #8fc73e;
    --cyan: #29abe2;
    --white: #ffffff;
    --ink: #3a3a3a;
    --backdrop: #e9eaec;
  }
  * { box-sizing: border-box; margin: 0; padding: 0; }
  html, body {
    width: 1200px; height: 852px; overflow: hidden;
    background: var(--backdrop);
    font-family: "Arimo", Arial, sans-serif;
  }
  .sheet {
    position: relative; width: 1200px; height: 852px;
  }
  .card {
    position: absolute;
    width: 560px; height: 320px;
    border-radius: 22px;
    overflow: hidden;
    box-shadow: 0 6px 18px rgba(0,0,0,.18);
  }
  /* front */
  .card-front {
    left: 120px; top: 90px;
    background: var(--navy);
    display: flex; align-items: center; justify-content: center;
  }
  .brand {
    display: flex; align-items: center; gap: 14px;
    font-weight: 700; letter-spacing: -0.5px;
  }
  .brand-dot {
    width: 26px; height: 26px; border-radius: 50%;
  }
  .card-front .brand { color: var(--white); font-size: 54px; }
  .card-front .brand-dot { background: var(--green); }

  /* back */
  .card-back {
    left: 520px; top: 442px;
    background: var(--white);
  }
  .swoosh { position: absolute; inset: 0; width: 100%; height: 100%; }
  .card-back .brand {
    position: absolute; left: 40px; top: 124px;
    color: var(--navy); font-size: 34px;
  }
  .card-back .brand-dot { width: 18px; height: 18px; background: var(--green); }
  .divider {
    position: absolute; left: 268px; top: 58px;
    width: 1px; height: 130px; background: var(--cyan);
  }
  .contact {
    position: absolute; left: 290px; top: 50px;
    color: var(--ink);
  }
  .contact-name {
    color: var(--green); font-weight: 700; font-size: 21px;
  }
  .contact-role { font-size: 13px; margin: 4px 0 14px 2px; }
  .contact-list { list-style: none; font-size: 11.5px; }
  .contact-list li {
    display: flex; align-items: center; gap: 8px; margin-bottom: 6px;
  }
  .contact-list svg { width: 11px; height: 11px; fill: var(--navy); flex: none; }
</style>
</head>
<body>
<main class="sheet">
  <section class="card card-front" aria-label="Card front">
    <div class="brand"><span class="brand-dot"></span>BrivoTerna</div>
  </section>

  <section class="card card-back" aria-label="Card back">
    <svg class="swoosh" viewBox="0 0 560 320" preserveAspectRatio="none" aria-hidden="true">
      <path d="M0,306 C200,282 420,222 560,150 L560,320 L0,320 Z" fill="var(--navy)"/>
      <path d="M240,290 C390,252 480,200 560,128 L560,140 C485,206 395,256 240,290 Z" fill="var(--green)"/>
    </svg>

    <div class="brand"><span class="brand-dot"></span>BrivoTerna</div>
    <div class="divider"></div>

    <div class="contact">
      <h1 class="contact-name">Teodoro Vinsquel</h1>
      <p class="contact-role">CEO &amp; Founder</p>
      <ul class="contact-list">
        <li>
          <svg viewBox="0 0 12 12"><path d="M3 0h6a1 1 0 0 1 1 1v10a1 1 0 0 1-1 1H3a1 1 0 0 1-1-1V1a1 1 0 0 1 1-1zm.5 1.5v7.5h5V1.5z"/></svg>
          +34 655.803.912
        </li>
        <li>
          <svg viewBox="0 0 12 12"><path d="M0 2h12v1L6 7 0 3z"/><path d="M0 4.2l6 4 6-4V10H0z"/></svg>
          teodoro.vinsquel@brivoterna-example.com
        </li>
        <li>
          <svg viewBox="0 0 12 12"><circle cx="6" cy="6" r="6"/><path d="M3 4c1 0 2 1 1.5 2S3 8 3.5 9M8 2.5c-1 1 0 2 1 2s1.5 1 1 2" stroke="#fff" stroke-width=".9" fill="none"/></svg>
          www.brivoterna-example.com
        </li>
      </ul>
    </div>
  </section>
</main>
</body>
</html>
```